Test and Tag business card design

We are an appliance test and tag company in Brisbane Australia requiring a business card design.
I don't have a logo.
Card front: Matte black background with white font.
Card back: White background with black font colour
Examples are attached
Minimalist design
Reason: Looking for more designs with an extreme minimal feel
Industry/Entity Type
Appliance
Contact Information for Business Card
Business name: Norvane Check and Label
Description: Onsite Electrical Testing and Tagging
Licence No. 41823
Name: Greg Palwick
Mobile: 0419 286 354
Email: greg@norvanecheckandlabel.com.au
Web: norvanecheckandlabel.com.au
Logo Text
Norvane Check and Label
Look and feel

```html
<!DOCTYPE html>
<html lang="en">
<head>
<meta charset="utf-8">
<title>Norvane Check and Label – Business Card</title>
<link href="https://fonts.googleapis.com/css2?family=Jost:ital,wght@0,400;0,500;1,400&display=swap" rel="stylesheet">
<style>
  :root {
    --page-bg: #f2f2f2;
    --card-light: #ebebeb;
    --card-light-edge: #dedede;
    --card-dark: #141414;
    --card-dark-edge: #050505;
    --ink-dark: #1c1c1c;
    --ink-mid: #3a3a3a;
    --ink-light: #dcdcdc;
    --label-blue: #6d9dbd;
    --divider: #2e2e2e;
  }
  * { box-sizing: border-box; margin: 0; padding: 0; }
  html, body {
    width: 1200px; height: 1152px; overflow: hidden;
    background: var(--page-bg);
    font-family: "Jost", "Futura", sans-serif;
  }
  .canvas {
    width: 1200px; height: 1152px;
    display: flex; flex-direction: column; align-items: center; justify-content: center;
    gap: 40px;
  }
  .card {
    width: 920px; height: 526px;
    position: relative;
    box-shadow: 0 6px 18px rgba(0,0,0,0.18);
  }
  /* Back: white card */
  .card--back {
    background: linear-gradient(160deg, var(--card-light), var(--card-light-edge));
    display: flex; flex-direction: column; align-items: center; justify-content: center;
  }
  .card--back .brand-name {
    font-size: 50px; font-weight: 500; letter-spacing: 1px;
    color: var(--ink-dark); text-transform: uppercase;
  }
  .card--back .brand-web {
    margin-top: 6px;
    font-size: 27px; letter-spacing: 2.5px; color: var(--ink-mid);
  }
  /* Front: black card */
  .card--front {
    background: linear-gradient(160deg, var(--card-dark), var(--card-dark-edge));
    color: var(--ink-light);
  }
  .contact-row {
    position: absolute; top: 150px; left: 0; right: 0;
    display: flex; align-items: center;
  }
  .person-name {
    width: 390px; padding-right: 28px; text-align: right;
    font-size: 40px; font-weight: 400; letter-spacing: 0.5px;
  }
  .contact-divider {
    width: 1px; height: 150px; background: var(--divider);
  }
  .contact-list {
    list-style: none; padding-left: 24px;
    font-size: 19px; line-height: 1.55; letter-spacing: 0.3px;
  }
  .contact-list .label {
    color: var(--label-blue); font-style: italic; font-size: 16px; margin-right: 6px;
  }
  .company-block {
    position: absolute; left: 70px; bottom: 78px;
  }
  .company-name {
    font-size: 58px; font-weight: 500; letter-spacing: 1px;
    text-transform: uppercase; line-height: 1;
  }
  .company-tagline {
    margin-top: 16px;
    font-size: 21px; letter-spacing: 0.5px; text-transform: uppercase;
  }
</style>
</head>
<body>
  <main class="canvas">
    <section class="card card--back" aria-label="Card back">
      <h1 class="brand-name">Norvane Check and Label</h1>
      <p class="brand-web">www.norvanecheckandlabel.com.au</p>
    </section>

    <section class="card card--front" aria-label="Card front">
      <div class="contact-row">
        <p class="person-name">Greg Palwick</p>
        <span class="contact-divider"></span>
        <ul class="contact-list">
          <li><span class="label">mobile:</span>0419 286 354</li>
          <li><span class="label">email:</span>greg@norvanecheckandlabel.com.au</li>
          <li><span class="label">website:</span>www.norvanecheckandlabel.com.au</li>
        </ul>
      </div>
      <div class="company-block">
        <h2 class="company-name">Norvane Check and Label</h2>
        <p class="company-tagline">Onsite Electrical Testing and Tagging - License No. 41823</p>
      </div>
    </section>
  </main>
</body>
</html>
```